International Clinical Software Company needs a new business card design

We are looking for a new business card design for our company that has recently expanded into the UK market, making us a multinational company.
After having rebranded our website and produced a new style guide, we are looking for a business card that is creative and attention grabbing, while being consistent with the style and colour scheme used on the new website, www.plumvora.example
We produce care management technology for the aged care market, but the main aspect we aim to communicate is the human element of our software, and the way it assists in providing better care for aged people, and stronger relationships between aged people and the staff that care for them.
Our current business card is a dark green with gold text, which makes the text quite difficult to read, not very aesthetically appealing and the colour scheme looks quite dated.
We would like something fresh and modern, that can still be colourful but doesn't use large blocks of dark colour, and uses the colours within our logo.
Something tying in with the leaves that are used in our logo could work quite nicely, along with the Autumn/Fall colours of soft greens, yellows and reds (also in our existing logo). However also happy to look at fresh, completely out of the box ideas we may not have yet considered.
Target Market(s)
The people that receive this business card work in the aged card or health industry and are either corporate/management level staff or clinical (Registered Nurses, care workers etc.)
Industry/Entity Type
Health Product
Contact Information for Business Card
Company Name - BrindlewayCare
Company locations: United Kingdom, Australia, New Zealand
Staff Details:
Staff name: Derek Mallow
Staff job title: Executive Chairman
Staff email: d.mallow@plumvora.example
Office phone number: 01742 918576
Font styles to use
Other font styles liked:
- Calibri
Requirements
Must have
- Must include the BrindlewayCare brand name in it's current font
- Must include logo (3 leaves in gold circle)
- Must include Business Card Details
Nice to have
- Elements of gold
- White space
- Something autumn themed but not too cliched
Should not have
- No blue - used by a major competitor and we would like to differentiate from them
- Large blocks of dark green colour (the green that appears in our leaves on the logo on our current business card is the background colour and it is far too dark)

```html
<!DOCTYPE html>
<html lang="en">
<head>
<meta charset="utf-8">
<title>BrindlewayCare – Business Card</title>
<link href="https://fonts.googleapis.com/css2?family=Arimo:wght@400;700&display=swap" rel="stylesheet">
<style>
  :root {
    --page-bg: #e8e3da;
    --card-bg: #ffffff;
    --gold: #b3a27c;
    --gold-soft: #ece4d2;
    --magenta: #c4175c;
    --text-grey: #6a6a6a;
    --divider: #dcdcdc;
  }
  * { margin: 0; padding: 0; box-sizing: border-box; }
  html, body {
    width: 1200px;
    height: 950px;
    overflow: hidden;
    background: var(--page-bg);
    font-family: "Arimo", Arial, sans-serif;
  }
  .card {
    position: absolute;
    left: 110px;
    top: 195px;
    width: 980px;
    height: 560px;
    background: var(--card-bg);
    box-shadow: 0 10px 30px rgba(0,0,0,0.18);
    overflow: hidden;
  }
  .social-links {
    position: absolute;
    top: 26px;
    right: 34px;
    display: flex;
    gap: 8px;
  }
  .social-dot {
    width: 26px;
    height: 26px;
    border-radius: 50%;
    background: var(--gold);
  }
  .brand {
    position: absolute;
    left: 70px;
    top: 110px;
    width: 360px;
    text-align: center;
  }
  .brand-mark {
    width: 150px;
    height: 150px;
    margin: 0 auto 26px;
    border-radius: 50%;
    background: var(--gold-soft);
    border: 6px solid var(--gold);
  }
  .brand-name {
    color: var(--gold);
    font-weight: 400;
    font-size: 40px;
    letter-spacing: 0.5px;
  }
  .divider {
    position: absolute;
    left: 480px;
    top: 90px;
    width: 1px;
    height: 270px;
    background: var(--divider);
  }
  .contact {
    position: absolute;
    left: 530px;
    top: 100px;
    color: var(--text-grey);
    font-size: 22px;
    line-height: 1.35;
  }
  .contact-name {
    color: var(--gold);
    font-weight: 700;
    font-size: 32px;
    line-height: 1.2;
  }
  .contact-title {
    color: var(--magenta);
    font-size: 23px;
    margin-bottom: 16px;
  }
  .contact-locations { margin-bottom: 6px; }
  .contact-line {
    display: flex;
    align-items: center;
    gap: 10px;
  }
  .contact-line svg { width: 20px; height: 20px; fill: var(--text-grey); flex: none; }
  .band-rule {
    position: absolute;
    left: 0;
    width: 100%;
    height: 3px;
    background: var(--magenta);
  }
  .band-rule.top { top: 418px; }
  .band-rule.bottom { top: 497px; }
  .web-band {
    position: absolute;
    left: 0;
    top: 424px;
    width: 100%;
    height: 70px;
    background: var(--gold);
    display: flex;
    align-items: center;
    justify-content: center;
  }
  .web-address {
    color: #ffffff;
    font-size: 24px;
    letter-spacing: 4px;
  }
</style>
</head>
<body>
  <div class="card">
    <div class="social-links" aria-label="Social media">
      <span class="social-dot"></span>
      <span class="social-dot"></span>
      <span class="social-dot"></span>
    </div>

    <div class="brand">
      <div class="brand-mark"></div>
      <div class="brand-name">BrindlewayCare</div>
    </div>

    <div class="divider"></div>

    <div class="contact">
      <div class="contact-name">Derek Mallow</div>
      <div class="contact-title">Executive Chairman</div>
      <div class="contact-locations">United Kingdom,<br>Australia, New Zealand</div>
      <div class="contact-line">
        <svg viewBox="0 0 24 24" aria-hidden="true"><path d="M6.6 10.8a15.1 15.1 0 0 0 6.6 6.6l2.2-2.2c.3-.3.7-.4 1-.2 1.1.4 2.3.6 3.6.6.6 0 1 .4 1 1V20c0 .6-.4 1-1 1A17 17 0 0 1 3 4c0-.6.4-1 1-1h3.5c.6 0 1 .4 1 1 0 1.3.2 2.5.6 3.6.1.3 0 .7-.2 1z"/></svg>
        <span>01742 918576</span>
      </div>
      <div class="contact-line">
        <svg viewBox="0 0 24 24" aria-hidden="true"><path d="M3 5h18v14H3z M3 5l9 7 9-7" fill="none" stroke="#6a6a6a" stroke-width="2"/></svg>
        <span>d.mallow@plumvora.example</span>
      </div>
    </div>

    <div class="band-rule top"></div>
    <div class="web-band"><span class="web-address">www.plumvora.example</span></div>
    <div class="band-rule bottom"></div>
  </div>
</body>
</html>
```